Harrow Grading LLC business card design

Excavation company business cards

Contact Information for Business Card

Harrow Grading LLC cell phone 208-417-6290 office phone 208-319-4856 harrowgradingllc@maplecove.com Driveways, site prep, retaining walls, septic systems, rock delivery

Colors

Designer to choose colors to be used in the design.

```html
<!DOCTYPE html>
<html lang="en">
<head>
<meta charset="utf-8">
<title>Harrow Grading LLC – Business Card</title>
<link rel="stylesheet" href="https://fonts.googleapis.com/css2?family=Arimo:wght@400;700&display=swap">
<style>
  :root {
    --page-bg: #e9e9ea;
    --card-bg: #2f2f31;
    --card-bg-deep: #262628;
    --orange: #f07a1f;
    --white: #ffffff;
    --text-light: #e6e6e6;
    --text-muted: #bdbdbd;
    --art-warm: #4a3328;
    --art-cool: #3a3a3d;
  }
  * { box-sizing: border-box; margin: 0; padding: 0; }
  html, body { width: 1200px; height: 802px; overflow: hidden; }
  body {
    background: var(--page-bg);
    font-family: "Arimo", Arial, sans-serif;
    position: relative;
  }
  .card {
    position: absolute;
    top: 246px;
    width: 540px;
    height: 309px;
    background: var(--card-bg);
    overflow: hidden;
    box-shadow: 0 10px 28px rgba(0,0,0,0.22);
  }
  .card--front { left: 45px; }
  .card--back  { left: 615px; background: var(--card-bg-deep); }

  /* Front */
  .front-art {
    position: absolute;
    right: 20px; top: 30px;
    width: 270px; height: 250px;
    background: radial-gradient(ellipse at 55% 55%, var(--art-warm) 0%, rgba(74,51,40,0.5) 45%, rgba(47,47,49,0) 75%);
  }
  .brand {
    position: absolute;
    left: 34px; top: 52px;
    display: flex; align-items: center; gap: 10px;
  }
  .brand-mark {
    width: 18px; height: 18px;
    background: var(--orange);
  }
  .brand-name {
    font-weight: 700;
    font-size: 22px;
    color: var(--orange);
    letter-spacing: 0.5px;
  }
  .person {
    position: absolute;
    left: 34px; top: 120px;
  }
  .person-name {
    font-weight: 700;
    font-size: 17px;
    color: var(--orange);
    letter-spacing: 0.5px;
  }
  .person-role {
    font-size: 12px;
    color: var(--text-light);
    margin-top: 3px;
  }
  .contact-list {
    position: absolute;
    left: 34px; top: 182px;
    list-style: none;
  }
  .contact-item {
    display: flex; align-items: center; gap: 10px;
    font-size: 13px;
    color: var(--text-light);
    height: 22px;
  }
  .contact-icon { width: 13px; height: 13px; flex: none; }
  .edge-tab {
    position: absolute;
    left: 0; top: 200px;
    width: 6px; height: 22px;
    background: var(--orange);
  }
  .bottom-band {
    position: absolute;
    left: 0; bottom: 0;
    width: 330px; height: 7px;
    background: var(--orange);
  }
  .side-band {
    position: absolute;
    right: 0; top: 0;
    width: 7px; height: 100%;
    background: var(--white);
  }

  /* Back */
  .back-art {
    position: absolute;
    right: 0; top: 0;
    width: 330px; height: 309px;
    background: linear-gradient(135deg, #1f1f21 0%, var(--art-cool) 45%, #4c4c50 70%, #232325 100%);
  }
  .back-brand {
    position: absolute;
    left: 30px; top: 44px;
    display: flex; align-items: center; gap: 8px;
  }
  .back-brand .brand-mark { width: 12px; height: 12px; }
  .back-brand .brand-name { font-size: 15px; }
  .service-list {
    position: absolute;
    left: 30px; top: 140px;
    list-style: none;
  }
  .service-item {
    display: flex; align-items: center; gap: 8px;
    font-size: 15px;
    color: var(--text-light);
    letter-spacing: 0.5px;
    height: 25px;
  }
  .service-item::before {
    content: "";
    width: 6px; height: 6px;
    border-radius: 50%;
    background: var(--orange);
  }
</style>
</head>
<body>

  <section class="card card--front">
    <div class="front-art" role="img" aria-label="Faint excavator with mountain peaks"></div>
    <div class="brand">
      <span class="brand-mark"></span>
      <span class="brand-name">Harrow Grading LLC</span>
    </div>
    <div class="person">
      <p class="person-name">MARCUS ELLERY</p>
      <p class="person-role">Manager</p>
    </div>
    <ul class="contact-list">
      <li class="contact-item">
        <svg class="contact-icon" viewBox="0 0 14 14"><rect x="3.5" y="1" width="7" height="12" rx="1.2" fill="none" stroke="#e6e6e6" stroke-width="1.3"/><circle cx="7" cy="11" r="0.8" fill="#e6e6e6"/></svg>
        208-417-6290
      </li>
      <li class="contact-item">
        <svg class="contact-icon" viewBox="0 0 14 14"><path d="M3 1.5l2.2 2.6-1.2 1.4c.8 1.8 2.2 3.2 4 4l1.4-1.2 2.6 2.2-1.4 2c-4.6-.4-8.6-4.4-9-9z" fill="#f07a1f"/></svg>
        208-319-4856
      </li>
      <li class="contact-item">
        <svg class="contact-icon" viewBox="0 0 14 14"><rect x="1" y="3" width="12" height="8.5" fill="#f07a1f"/><path d="M1 3l6 5 6-5" fill="none" stroke="#2f2f31" stroke-width="1.2"/></svg>
        harrowgradingllc@maplecove.com
      </li>
    </ul>
    <span class="edge-tab"></span>
    <span class="bottom-band"></span>
    <span class="side-band"></span>
  </section>

  <section class="card card--back">
    <div class="back-art" role="img" aria-label="Embossed excavator silhouette over mountain peaks"></div>
    <div class="back-brand">
      <span class="brand-mark"></span>
      <span class="brand-name">Harrow Grading LLC</span>
    </div>
    <ul class="service-list">
      <li class="service-item">DRIVEWAYS</li>
      <li class="service-item">SITE PREP</li>
      <li class="service-item">RETAINING WALLS</li>
      <li class="service-item">SEPTIC SYSTEMS</li>
      <li class="service-item">ROCK DELIVERY</li>
    </ul>
  </section>

</body>
</html>
```